Cedar Brook Stables, LLC

Equestrian business card to promote equine retirement, farm sitting, short term board. Located in Aiken, SC.
Updates
Updated color schemes.
Contact Information for Business Card
Contact info, description of work.
Colors
0094D4
00A9DD
6FCCEA
C7EBF8
E9F6FB
59FF00
82FF00
B8FF75
E3FFCB
F4FFEA
F0912C
F2A743
F7CA91
FBE8D2
FDF5EE

```html
<!DOCTYPE html>
<html lang="en">
<head>
<meta charset="utf-8">
<title>Cedar Brook Stables – Business Card</title>
<link href="https://fonts.googleapis.com/css2?family=Poppins:wght@400;500;600;700&display=swap" rel="stylesheet">
<style>
  :root {
    --stage: #d9d9d9;
    --farm-green: #006a00;
    --sun-yellow: #ffd63f;
    --sun-orange: #ffb800;
    --ink: #222222;
    --rule: #9a9a9a;
    --paper: #ffffff;
  }
  * { margin: 0; padding: 0; box-sizing: border-box; }
  html, body {
    width: 1200px; height: 1200px; overflow: hidden;
    background: var(--stage);
    font-family: "Poppins", sans-serif;
  }
  .stage { position: relative; width: 1200px; height: 1200px; }
  .card {
    position: absolute; top: 303px; height: 594px;
    box-shadow: 4px 4px 3px rgba(0,0,0,0.55);
    overflow: hidden;
  }
  /* Front */
  .card-front { left: 200px; width: 369px; background: var(--farm-green); }
  .pasture-scene {
    position: absolute; left: 0; top: 0; width: 100%; height: 380px;
    background: linear-gradient(180deg, var(--sun-orange) 0%, var(--sun-yellow) 45%, var(--sun-yellow) 70%, var(--farm-green) 100%);
  }
  .services {
    position: absolute; left: 0; width: 100%; top: 425px;
    list-style: none; text-align: center;
    color: var(--paper); font-weight: 500; font-size: 21px; line-height: 41px;
  }
  /* Back */
  .card-back { left: 599px; width: 364px; background: var(--paper); text-align: center; color: var(--ink); }
  .brand-mark {
    position: absolute; left: 147px; top: 90px; width: 70px; height: 70px;
    border: 3px solid var(--farm-green); border-radius: 50%;
  }
  .brand-name {
    position: absolute; left: 0; width: 100%; top: 178px;
    font-weight: 600; font-size: 23px; line-height: 30px; letter-spacing: 0.5px;
    color: var(--ink);
  }
  .person-name {
    position: absolute; left: 0; width: 100%; top: 334px;
    color: var(--farm-green); font-weight: 700; font-size: 25px; letter-spacing: 0.5px;
  }
  .person-title { position: absolute; left: 0; width: 100%; top: 364px; font-size: 16px; }
  .contact-icons {
    position: absolute; left: 87px; width: 190px; top: 396px; height: 25px;
    display: flex; justify-content: center; align-items: center; gap: 4px;
  }
  .contact-icons .rule { flex: 1; height: 1px; background: var(--rule); }
  .contact-icons .rule:first-child { margin-right: 4px; }
  .contact-icons .rule:last-child { margin-left: 4px; }
  .icon-box {
    width: 25px; height: 25px; background: var(--farm-green); border-radius: 3px;
    display: flex; align-items: center; justify-content: center;
  }
  .contact-lines {
    position: absolute; left: 0; width: 100%; top: 428px;
    font-size: 16px; line-height: 21px;
  }
  .divider { position: absolute; left: 89px; width: 195px; top: 507px; height: 1px; background: var(--rule); }
  .address { position: absolute; left: 0; width: 100%; top: 520px; font-size: 16px; line-height: 21px; }
</style>
</head>
<body>
<main class="stage">
  <section class="card card-front">
    <div class="pasture-scene" role="img" aria-label="Illustration of a horse silhouette walking through grass against a yellow sunburst"></div>
    <ul class="services">
      <li>SHORT TERM BOARD</li>
      <li>FARM SITTING</li>
      <li>EQUINE RETIREMENT</li>
    </ul>
  </section>

  <section class="card card-back">
    <div class="brand-mark"></div>
    <p class="brand-name">CEDAR BROOK STABLES<br>LLC</p>

    <h1 class="person-name">DANIEL HARPER</h1>
    <p class="person-title">Managing Director</p>

    <div class="contact-icons">
      <span class="rule"></span>
      <span class="icon-box">
        <svg width="15" height="15" viewBox="0 0 24 24" aria-hidden="true"><path fill="#fff" d="M6.6 10.8a15 15 0 0 0 6.6 6.6l2.2-2.2c.3-.3.7-.4 1-.2 1.1.4 2.3.6 3.6.6.6 0 1 .4 1 1V20c0 .6-.4 1-1 1A17 17 0 0 1 3 4c0-.6.4-1 1-1h3.5c.6 0 1 .4 1 1 0 1.3.2 2.5.6 3.6.1.3 0 .7-.2 1z"/></svg>
      </span>
      <span class="icon-box">
        <svg width="16" height="12" viewBox="0 0 16 12" aria-hidden="true"><rect x="0.75" y="0.75" width="14.5" height="10.5" fill="none" stroke="#fff" stroke-width="1.5"/><path d="M1 1l7 6 7-6M1 11l5-5M15 11l-5-5" fill="none" stroke="#fff" stroke-width="1.2"/></svg>
      </span>
      <span class="icon-box">
        <svg width="15" height="15" viewBox="0 0 16 16" aria-hidden="true"><circle cx="8" cy="8" r="6.5" fill="none" stroke="#fff" stroke-width="1.5"/><ellipse cx="8" cy="8" rx="2.8" ry="6.5" fill="none" stroke="#fff" stroke-width="1.2"/><path d="M1.5 8h13" stroke="#fff" stroke-width="1.2"/></svg>
      </span>
      <span class="rule"></span>
    </div>

    <p class="contact-lines">044-123 456 789<br>info@webname.com<br>www.websitename.com</p>
    <div class="divider"></div>
    <p class="address">421, Address line goes here<br>45452,Country Name</p>
  </section>
</main>
</body>
</html>
```